PWNF Traditional Business Card Project

Please see attached....just a simple business card... on attachment- please use the exact font, style, etc as the attached "Ned Farley Broughton" card... however, replace with the "Walter Augustin Pryde" text and address below the card.

```html
<!DOCTYPE html>
<html lang="en">
<head>
<meta charset="utf-8">
<title>PWNF Business Card – Walter Augustin Pryde</title>
<link rel="stylesheet" href="https://fonts.googleapis.com/css2?family=Tinos:wght@400&display=swap">
<style>
  :root {
    --backdrop: #e9e6e1;
    --card-frame: #858585;
    --card-paper: #d8d8da;
    --corner-mark: #ffffff;
    --ink: #141414;
  }
  html, body {
    margin: 0;
    padding: 0;
    width: 1200px;
    height: 902px;
    overflow: hidden;
    background: var(--backdrop);
  }
  .business-card {
    position: absolute;
    left: 100px;
    top: 165px;
    width: 1000px;
    height: 572px;
    background: var(--card-frame);
    box-shadow: 0 6px 24px rgba(0,0,0,0.18);
    font-family: "Tinos", "Times New Roman", serif;
    color: var(--ink);
  }
  .card-paper {
    position: absolute;
    inset: 18px;
    background: var(--card-paper);
  }
  .corner-mark {
    position: absolute;
    width: 56px;
    height: 56px;
    border: 0 solid var(--corner-mark);
  }
  .corner-mark.top-left { left: 18px; top: 18px; border-left-width: 12px; border-top-width: 12px; }
  .corner-mark.top-right { right: 18px; top: 18px; border-right-width: 12px; border-top-width: 12px; }
  .corner-mark.bottom-left { left: 18px; bottom: 18px; border-left-width: 12px; border-bottom-width: 12px; }
  .corner-mark.bottom-right { right: 18px; bottom: 18px; border-right-width: 12px; border-bottom-width: 12px; }

  .firm-name {
    position: absolute;
    left: 46px;
    top: 38px;
    margin: 0;
    font-weight: 400;
    line-height: 1;
  }
  .firm-name .firm-primary {
    display: block;
    font-size: 29px;
    font-variant: small-caps;
    letter-spacing: 0.5px;
  }
  .firm-name .firm-secondary {
    display: block;
    margin: 4px 0 0 38px;
    font-size: 18px;
    letter-spacing: 0.8px;
  }

  .attorney {
    position: absolute;
    left: 0;
    right: 0;
    top: 225px;
    text-align: center;
  }
  .attorney-name {
    margin: 0;
    font-size: 56px;
    font-weight: 400;
    font-variant: small-caps;
    letter-spacing: 1px;
    line-height: 1;
  }
  .attorney-title {
    margin: 14px 0 0;
    font-size: 22px;
    letter-spacing: 0.6px;
  }

  .contact {
    position: absolute;
    bottom: 34px;
    margin: 0;
    font-size: 23px;
    line-height: 30px;
    font-style: normal;
    letter-spacing: 0.3px;
  }
  .contact.office { left: 48px; }
  .contact.lines { right: 46px; text-align: right; bottom: 42px; }
</style>
</head>
<body>
  <div class="business-card">
    <div class="card-paper"></div>
    <div class="corner-mark top-left"></div>
    <div class="corner-mark top-right"></div>
    <div class="corner-mark bottom-left"></div>
    <div class="corner-mark bottom-right"></div>

    <h2 class="firm-name">
      <span class="firm-primary">Pacific West</span>
      <span class="firm-secondary">NEWFIELD FIRM, PLC</span>
    </h2>

    <div class="attorney">
      <h1 class="attorney-name">Walter Augustin Pryde</h1>
      <p class="attorney-title">ATTORNEY AT LAW</p>
    </div>

    <address class="contact office">
      2740 ALDER STREET, SUITE B<br>
      MAPLE GROVE, CA 91802<br>
      www.lawpwnf.com
    </address>

    <address class="contact lines">
      TEL (555) 214-3380<br>
      FAX (555) 214-3391<br>
      wpryde@lawpwnf.com
    </address>
  </div>
</body>
</html>
```